New Dental Office Needs an Attractive and user friendly Website Designed

I need a website for a new dental office. The Name is Harrowfield Dentistry. I would like a Modern design with a user friendly interface and usability.
I would like a landing page, a page that lists the services we offer: Cosmetic Dentistry, Implants, Dental Hygiene, Emergency Services, Restorations, Dentures
Target Market(s)
Mid to upper class
Industry/Entity Type
Dentistry
Coding
Number of Pages Required
1 page
Requirements
Must have
- Landing page that has a scheduling option, Procedures, operating hours, and contact us info
Nice to have
- Appealing design, Soft comforting colors. Easy to navigate page, Modern and professional.

```html
<!DOCTYPE html>
<html lang="en">
<head>
<meta charset="utf-8">
<title>Harrowfield Dentistry</title>
<link href="https://fonts.googleapis.com/css2?family=Playfair+Display:wght@400;600;700;800&family=DM+Sans:wght@400;500;600;700&display=swap" rel="stylesheet">
<style>
:root{
  --ink:#141414;
  --ink-soft:#3a3a3a;
  --muted:#6f6f6f;
  --line:#e6e6e6;
  --paper:#ffffff;
  --mist:#f4f5f7;
  --sky:#dfeaf3;
  --star:#f2b824;
  --serif:"Playfair Display", Georgia, serif;
  --sans:"DM Sans", Arial, sans-serif;
}
*{box-sizing:border-box;margin:0;padding:0}
html,body{width:1200px;height:4823px;overflow:hidden}
body{position:relative;background:var(--paper);font-family:var(--sans);color:var(--ink)}
.abs{position:absolute}
.serif{font-family:var(--serif)}
svg{display:block}

/* buttons */
.btn{position:absolute;display:flex;align-items:center;justify-content:space-between;border-radius:30px;font-family:var(--sans);font-weight:600;font-size:12px;padding:0 5px 0 16px}
.btn-dark{background:var(--ink);color:#fff}
.btn-light{background:#fff;color:var(--ink)}
.btn-ic{width:32px;height:32px;border-radius:50%;display:flex;align-items:center;justify-content:center}
.btn-dark .btn-ic{background:#fff}
.btn-light .btn-ic{background:var(--ink)}

/* hero */
.hero{left:0;top:0;width:1200px;height:603px;background:linear-gradient(100deg,#1c1d20 0%,#2c2f33 40%,#5d6570 70%,#8d96a0 100%)}
.topbar{left:0;top:0;width:1200px;height:37px;border-bottom:1px solid rgba(255,255,255,.18);color:#fff;font-size:10px}
.topbar .item{position:absolute;top:9px;display:flex;align-items:center;gap:10px;white-space:nowrap}
.ic-circle{width:20px;height:20px;border-radius:50%;background:#fff;display:flex;align-items:center;justify-content:center}
.soc{width:20px;height:20px;border-radius:50%;border:1px solid rgba(255,255,255,.6)}
.logo{position:absolute;font-family:var(--serif);font-weight:400;line-height:1;text-align:center}
.logo .l1{font-size:34px}
.logo .l2{font-size:13px;letter-spacing:5px;margin-top:3px}
.nav{position:absolute;top:74px;color:#fff;font-size:10px;font-weight:500}
.nav span{position:absolute;white-space:nowrap}
.nav .on{border-bottom:1px solid #fff;padding-bottom:6px}
.badge{left:93px;top:171px;height:28px;padding:0 16px;background:#fff;border-radius:14px;font-size:10px;font-weight:700;display:flex;align-items:center}
.hero-title{left:93px;top:212px;color:#fff;font-family:var(--serif);line-height:1.05;white-space:nowrap}
.hero-title .a{font-size:58px;font-weight:400;display:block}
.hero-title .b{font-size:62px;font-weight:800;display:block;letter-spacing:1px}
.hero-sub{left:93px;top:358px;width:480px;color:#eee;font-size:13px;line-height:1.6}

.infocard{left:193px;top:554px;width:818px;height:111px;background:#fff;border-radius:14px;box-shadow:0 10px 30px rgba(0,0,0,.08);display:flex;align-items:center}
.info{flex:1;display:flex;align-items:center;gap:14px;padding-left:30px;border-right:1px solid var(--line);height:60px}
.info:last-child{border-right:none}
.info .sq{width:42px;height:42px;border-radius:8px;background:var(--ink);display:flex;align-items:center;justify-content:center;flex-shrink:0}
.info small{display:block;font-size:10px;color:var(--ink-soft)}
.info b{font-size:14px}
.info .t{font-size:11px;line-height:1.35}

/* about */
.about-photo{left:146px;top:796px;width:309px;height:309px;border-radius:50%;background:radial-gradient(circle at 55% 40%,#e9d6cc,#9fb6c7 60%,#5f7484)}
.about-tag{left:345px;top:1030px;width:155px;height:82px;background:#fff;border-radius:12px;box-shadow:0 8px 20px rgba(0,0,0,.08);padding:10px 12px}
.about-tag .name{font-family:var(--serif);font-size:15px;text-align:center;line-height:1}
.about-tag .sub{font-family:var(--serif);font-size:7px;letter-spacing:3px;text-align:center}
.avatars{display:flex;margin-top:8px;align-items:center}
.avatars i{width:20px;height:20px;border-radius:50%;border:2px solid #fff;margin-right:-6px;background:#c9a995}
.avatars i:nth-child(2){background:#a98572}.avatars i:nth-child(3){background:#d8b9a8}
.avatars span{margin-left:14px;font-size:9px;line-height:1.1;color:var(--ink-soft)}
.about-title{left:618px;top:822px;width:440px;font-family:var(--serif);font-size:31px;font-weight:700;line-height:1.25}
.about-kicker{left:618px;top:995px;font-size:14px;font-weight:700;letter-spacing:.3px}

/* section heads */
.sec-title{font-family:var(--serif);font-weight:700;font-size:40px;line-height:1.25}
.center{text-align:center;left:0;width:1200px}

/* services */
.svc{width:236px;height:343px;background:#fff;border-radius:14px;box-shadow:0 8px 24px rgba(0,0,0,.08)}
.svc .ph{position:absolute;left:12px;top:10px;width:212px;height:154px;border-radius:8px}
.svc .icon{position:absolute;left:26px;top:132px;width:52px;height:52px;border-radius:8px;background:#fff;box-shadow:0 4px 10px rgba(0,0,0,.1);display:flex;align-items:center;justify-content:center}
.svc .icon i{width:38px;height:38px;border-radius:6px;background:var(--mist);display:flex;align-items:center;justify-content:center}
.svc h3{position:absolute;left:26px;top:206px;font-size:18px;font-weight:700;white-space:nowrap}
.svc p{position:absolute;left:26px;top:236px;width:180px;font-size:11px;line-height:1.55;color:var(--ink-soft)}
.svc .go{position:absolute;right:0;bottom:0;width:52px;height:52px;border-radius:12px 0 12px 0;background:#f0f0f0;display:flex;align-items:center;justify-content:center}
.svc .go i{width:40px;height:40px;border-radius:8px;background:#fff;display:flex;align-items:center;justify-content:center}
.svc .go.on i{background:var(--ink)}
.dots{display:flex;gap:8px}
.dots i{width:36px;height:14px;border-radius:7px;background:#eee;display:flex;align-items:center;justify-content:center}
.dots i.on{width:42px;background:var(--ink)}

/* why */
.why-a{left:163px;top:2137px;width:214px;height:181px;border-radius:10px;background:linear-gradient(135deg,#f2d2c9,#e7b7ad);z-index:2;border:5px solid #fff}
.why-b{left:327px;top:2082px;width:235px;height:286px;border-radius:10px;background:linear-gradient(135deg,#d8c3b6,#4b6b8c)}
.feat{left:640px;width:438px;height:87px;background:#fff;box-shadow:0 6px 18px rgba(0,0,0,.07);border-radius:4px}
.feat .fi{position:absolute;left:8px;top:8px;width:70px;height:70px;border-radius:4px;background:#eceef0;display:flex;align-items:center;justify-content:center}
.feat .fi.dark{background:var(--ink)}
.feat h4{position:absolute;left:97px;top:12px;font-size:16px;font-weight:700}
.feat p{position:absolute;left:97px;top:37px;width:320px;font-size:10.5px;line-height:1.5;color:var(--ink-soft)}

/* reviews */
.rev{top:2617px;height:318px;border:5px solid #2a2a2a;border-radius:12px;background:#fff;overflow:hidden}
.rev .ba{position:absolute;left:6px;width:242px;height:146px;border-radius:4px;background:linear-gradient(180deg,#c98f86,#f0e7e2 55%,#b77a71)}
.lbl{position:absolute;background:#fff;font-size:8px;font-weight:700;padding:2px 6px;border-radius:2px}
.stars{display:flex;gap:4px}
.rev h3{font-size:22px;font-weight:700;line-height:1.3}
.rev .q{font-size:12px;line-height:1.6;color:var(--ink-soft)}
.gdot{width:22px;height:22px;border-radius:50%;background:#e8e8e8}

/* team */
.tm{top:3283px;height:300px;background:#fff;box-shadow:0 6px 22px rgba(0,0,0,.08);border-radius:6px;overflow:hidden}
.tm .ph{position:absolute;left:0;top:0;width:100%;height:300px;background:linear-gradient(180deg,#f3f3f3,#d7dde2)}
.tm .nm{position:absolute;left:10px;right:10px;bottom:12px;height:62px;background:#fff;border-radius:6px;text-align:center;padding-top:14px;box-shadow:0 2px 8px rgba(0,0,0,.06)}
.tm .nm b{font-size:17px;display:block;color:#1b2b45;white-space:nowrap}
.tm .nm small{font-size:9px;color:var(--muted)}
.plus{position:absolute;left:22px;bottom:64px;width:24px;height:24px;border-radius:50%;background:var(--ink);color:#fff;font-size:16px;display:flex;align-items:center;justify-content:center;z-index:2}

/* form */
.band{left:0;top:4216px;width:1200px;height:607px;background:var(--ink)}
.form{left:191px;top:3837px;width:818px;height:497px;background:#f1f1f1;border-radius:24px}
.lab{position:absolute;font-size:10px;color:var(--ink-soft)}
.fld{position:absolute;height:41px;background:#fff;border-radius:3px;font-size:11px;display:flex;align-items:center;justify-content:space-between;padding:0 10px}
.fld .tick{width:13px;height:13px;border-radius:50%;background:var(--ink);display:flex;align-items:center;justify-content:center}
.fld .sel{width:14px;height:14px;border-radius:50%;border:1px solid #666;display:flex;align-items:center;justify-content:center}
.confirm{left:266px;top:4218px;width:204px;height:41px;background:var(--ink);color:#fff;font-size:11px;font-weight:600;display:flex;align-items:center;justify-content:center;border-radius:2px}

/* footer */
.foot{color:#fff}
.foot h5{position:absolute;font-size:16px;font-weight:700;letter-spacing:.3px}
.foot .row{position:absolute;display:flex;gap:12px;font-size:10px;line-height:1.5}
.foot .row b{font-size:16px}
.foot ul{position:absolute;list-style:none;font-size:11px}
.foot li{height:34px}
.foot li::before{content:"»";margin-right:10px}
.sqsoc{width:26px;height:26px;background:#333}
.map{left:880px;top:4455px;width:180px;height:141px;background:linear-gradient(135deg,#d9ecd8,#f3f1ea 50%,#cfe2ee);border:3px solid #fff}
</style>
</head>
<body>

<!-- HERO -->
<div class="abs hero" role="img" aria-label="Dentist treating a patient reclining in a modern dental chair"></div>
<div class="abs topbar">
  <div class="item" style="left:100px"><span class="ic-circle"><svg width="10" height="10" viewBox="0 0 24 24"><path d="M12 2a7 7 0 0 0-7 7c0 5 7 13 7 13s7-8 7-13a7 7 0 0 0-7-7zm0 9.5A2.5 2.5 0 1 1 12 6.5a2.5 2.5 0 0 1 0 5z" fill="#141414"/></svg></span>Location: <b>45 Harrowfield Lane, Your City</b></div>
  <div class="item" style="left:392px"><span class="ic-circle"><svg width="10" height="10" viewBox="0 0 24 24"><path d="M6.6 10.8a15 15 0 0 0 6.6 6.6l2.2-2.2a1 1 0 0 1 1-.3 11 11 0 0 0 3.6.6 1 1 0 0 1 1 1V20a1 1 0 0 1-1 1A17 17 0 0 1 3 4a1 1 0 0 1 1-1h3.5a1 1 0 0 1 1 1c0 1.3.2 2.5.6 3.6a1 1 0 0 1-.3 1z" fill="#141414"/></svg></span>Call Us: <b>(555) 014-2367</b></div>
  <div class="item" style="left:986px">Follow Us: <span class="soc"></span><span class="soc"></span></div>
</div>
<div class="logo" style="left:93px;top:56px;color:#fff"><div class="l1">Harrowfield</div><div class="l2">DENTISTRY</div></div>
<div class="nav">
  <span class="on" style="left:502px">HOME</span>
  <span style="left:578px">ABOUT</span>
  <span style="left:660px">SERVICES</span>
  <span style="left:758px">PROCEDURES</span>
  <span style="left:882px">CONTACT</span>
</div>
<div class="btn btn-light" style="left:973px;top:59px;width:133px;height:40px;font-size:10px">LET'S TALK<span class="btn-ic"><svg width="12" height="12" viewBox="0 0 12 12"><path d="M3 9 9 3M4 3h5v5" stroke="#fff" stroke-width="1.6" fill="none"/></svg></span></div>

<div class="abs badge">24/7 SERVICE AVAILABLE</div>
<div class="abs" style="left:280px;top:185px;width:110px;height:1px;background:rgba(255,255,255,.7)"></div>
<div class="abs" style="left:282px;top:181px;width:9px;height:9px;border-radius:50%;background:#fff"></div>
<h1 class="abs hero-title"><span class="a">Gentle Care for</span><span class="b">BRIGHT SMILES</span></h1>
<p class="abs hero-sub">Experience top-quality dental care focused on your smile's health &amp; beauty. Trust us to create a brighter, healthier tomorrow.</p>
<div class="btn btn-light" style="left:93px;top:440px;width:218px;height:42px">Schedule Appointment<span class="btn-ic"><svg width="12" height="12" viewBox="0 0 12 12"><path d="M3 9 9 3M4 3h5v5" stroke="#fff" stroke-width="1.6" fill="none"/></svg></span></div>

<div class="abs infocard">
  <div class="info"><span class="sq"><svg width="18" height="18" viewBox="0 0 24 24"><path d="M6.6 10.8a15 15 0 0 0 6.6 6.6l2.2-2.2a1 1 0 0 1 1-.3 11 11 0 0 0 3.6.6 1 1 0 0 1 1 1V20a1 1 0 0 1-1 1A17 17 0 0 1 3 4a1 1 0 0 1 1-1h3.5a1 1 0 0 1 1 1c0 1.3.2 2.5.6 3.6a1 1 0 0 1-.3 1z" fill="#fff"/></svg></span><div><small>Need a Dental Services?</small><b>(555) 014-2367</b></div></div>
  <div class="info"><span class="sq"><svg width="20" height="20" viewBox="0 0 24 24"><circle cx="12" cy="12" r="9" fill="#fff"/><path d="M12 7v5l3 2" stroke="#141414" stroke-width="2" fill="none"/></svg></span><div class="t"><small>Opening Hours</small>Mon to Sat <b style="font-size:11px">9:00AM</b> to <b style="font-size:11px">6:00PM</b></div></div>
  <div class="info"><span class="sq"><svg width="18" height="18" viewBox="0 0 24 24"><path d="M12 2a7 7 0 0 0-7 7c0 5 7 13 7 13s7-8 7-13a7 7 0 0 0-7-7zm0 9.5A2.5 2.5 0 1 1 12 6.5a2.5 2.5 0 0 1 0 5z" fill="#fff"/></svg></span><div class="t"><small>Our Location</small>88 Willow Crest Road<br>Brookdale, CA 90210</div></div>
</div>

<!-- ABOUT -->
<section>
  <div class="abs about-photo" role="img" aria-label="Smiling patient giving a thumbs up from the dental chair"></div>
  <div class="abs about-tag"><div class="name">Harrowfield</div><div class="sub">DENTISTRY</div><div class="avatars"><i></i><i></i><i></i><span>09K + Happy<br>Customers</span></div></div>
  <h2 class="abs about-title">We provide Gentle, Modern Dental care in a calm, Welcoming environment for Every Smile.</h2>
  <div class="abs about-kicker">NEED A DENTAL SERVICES? WE TAKE CARE OF YOU.</div>
  <div class="btn btn-dark" style="left:618px;top:1044px;width:201px;height:40px;font-size:11px">Schedule Appointment<span class="btn-ic"><svg width="12" height="12" viewBox="0 0 12 12"><path d="M3 9 9 3M4 3h5v5" stroke="#141414" stroke-width="1.6" fill="none"/></svg></span></div>
</section>

<!-- SERVICES -->
<h2 class="abs center sec-title" style="top:1272px">Turning Your Smile Into<br>An Experience</h2>
<div class="abs svc" style="left:88px;top:1417px"><div class="ph" role="img" aria-label="Woman smiling against a teal background" style="background:linear-gradient(135deg,#5fc7cc,#2c9fa8)"></div><div class="icon"><i><svg width="20" height="20" viewBox="0 0 24 24"><path d="M7 3c-3 0-4 3-3 6l2 11c.3 1 1.7 1 2 0l1.5-6h5l1.5 6c.3 1 1.7 1 2 0l2-11c1-3 0-6-3-6-2 0-3 1-5 1S9 3 7 3z" fill="#141414"/></svg></i></div><h3>Cosmetic Dentistry</h3><p>Enhance your smile with whitening, veneers, and natural-looking restorations.</p><div class="go"><i><svg width="14" height="14" viewBox="0 0 12 12"><path d="M3 9 9 3M4 3h5v5" stroke="#141414" stroke-width="1.6" fill="none"/></svg></i></div></div>
<div class="abs svc" style="left:350px;top:1417px"><div class="ph" role="img" aria-label="Patient with shade guide beside her teeth" style="background:linear-gradient(135deg,#8a8a8a,#3a3a3a)"></div><div class="icon"><i><svg width="20" height="20" viewBox="0 0 24 24"><path d="M7 3c-3 0-4 3-3 6l2 11c.3 1 1.7 1 2 0l1.5-6h5l1.5 6c.3 1 1.7 1 2 0l2-11c1-3 0-6-3-6-2 0-3 1-5 1S9 3 7 3z" fill="#141414"/></svg></i></div><h3>Implants</h3><p>Permanent, comfortable solutions to restore missing teeth and confidence.</p><div class="go on"><i><svg width="14" height="14" viewBox="0 0 12 12"><path d="M3 9 9 3M4 3h5v5" stroke="#fff" stroke-width="1.6" fill="none"/></svg></i></div></div>
<div class="abs svc" style="left:612px;top:1417px"><div class="ph" role="img" aria-label="Dentist examining a patient's teeth" style="background:linear-gradient(135deg,#a9c3db,#3b6f9c)"></div><div class="icon"><i><svg width="20" height="20" viewBox="0 0 24 24"><path d="M7 3c-3 0-4 3-3 6l2 11c.3 1 1.7 1 2 0l1.5-6h5l1.5 6c.3 1 1.7 1 2 0l2-11c1-3 0-6-3-6-2 0-3 1-5 1S9 3 7 3z" fill="#141414"/></svg></i></div><h3>Dental Hygiene</h3><p>Preventive cleanings and checkups to keep your mouth healthy and fresh.</p><div class="go"><i><svg width="14" height="14" viewBox="0 0 12 12"><path d="M3 9 9 3M4 3h5v5" stroke="#141414" stroke-width="1.6" fill="none"/></svg></i></div></div>
<div class="abs svc" style="left:885px;top:1417px"><div class="ph" role="img" aria-label="Dental team treating a patient in gloves and masks" style="background:linear-gradient(135deg,#5a87c7,#1e3f7a)"></div><div class="icon"><i><svg width="20" height="20" viewBox="0 0 24 24"><path d="M6 19v-6a6 6 0 0 1 12 0v6zM4 19h16v2H4z" fill="#141414"/></svg></i></div><h3>Emergency Services</h3><p>Prompt care for pain, injuries, or unexpected dental issues—when you need it most.</p><div class="go"><i><svg width="14" height="14" viewBox="0 0 12 12"><path d="M3 9 9 3M4 3h5v5" stroke="#141414" stroke-width="1.6" fill="none"/></svg></i></div></div>
<div class="abs dots" style="left:556px;top:1805px"><i><svg width="6" height="8" viewBox="0 0 6 8"><path d="M5 1 2 4l3 3" stroke="#555" fill="none"/></svg></i><i class="on"><svg width="6" height="8" viewBox="0 0 6 8"><path d="m1 1 3 3-3 3" stroke="#fff" fill="none"/></svg></i></div>

<!-- WHY -->
<h2 class="abs sec-title" style="left:159px;top:1935px">Why Choose<br>Harrowfield Denistry?</h2>
<div class="btn btn-dark" style="left:885px;top:1980px;width:201px;height:40px;font-size:11px">Schedule Appointment<span class="btn-ic"><svg width="12" height="12" viewBox="0 0 12 12"><path d="M3 9 9 3M4 3h5v5" stroke="#141414" stroke-width="1.6" fill="none"/></svg></span></div>
<div class="abs why-a" role="img" aria-label="Close-up of a bright white smile"></div>
<div class="abs why-b" role="img" aria-label="Patient smiling while a dentist works"></div>
<div class="abs feat" style="top:2084px"><div class="fi"><svg width="30" height="30" viewBox="0 0 24 24"><circle cx="12" cy="6" r="3" fill="#141414"/><path d="M5 21l3-9h8l3 9z" fill="#141414"/></svg></div><h4>Comfort-First Experience</h4><p>From soothing colors and gentle lighting to a warm, welcoming team that treats you like family.</p></div>
<div class="abs feat" style="top:2185px"><div class="fi dark"><svg width="30" height="30" viewBox="0 0 24 24"><rect x="3" y="4" width="18" height="13" rx="1" fill="none" stroke="#fff" stroke-width="1.6"/><path d="M9 21h6M12 17v4" stroke="#fff" stroke-width="1.6"/></svg></div><h4>Modern Dental Technology</h4><p>We use techniques to ensure fast, precise, and pain-free treatments that help you feel confident and cared for.</p></div>
<div class="abs feat" style="top:2284px"><div class="fi"><svg width="30" height="30" viewBox="0 0 24 24"><circle cx="12" cy="12" r="8" fill="none" stroke="#141414" stroke-width="2"/><path d="M12 4a8 8 0 0 0 0 16z" fill="#141414"/></svg></div><h4>Patient Education &amp; Transparency</h4><p>We explain every step and provide honest, clear communication.</p></div>

<!-- REVIEWS -->
<h2 class="abs center sec-title" style="top:2518px">Real Stories from Happy Smiles.</h2>
<div class="abs rev" style="left:-40px;width:237px"><div class="abs" style="left:40px;top:60px;width:180px"><h3>Easy booking, warm home.</h3><p class="q" style="margin-top:14px">Diam adipiscing elit, sed laoreet dolore magna ad minim.</p></div><div class="gdot abs" style="left:165px;top:240px"></div></div>
<div class="abs rev" style="left:219px;width:728px">
  <div class="ba" style="top:6px" role="img" aria-label="Teeth before whitening"></div>
  <div class="ba" style="top:156px" role="img" aria-label="Teeth after whitening"></div>
  <span class="lbl" style="left:12px;top:12px">BEFORE</span><span class="lbl" style="left:196px;top:285px">AFTER</span>
  <div class="abs" style="left:115px;top:136px;width:26px;height:26px;border-radius:50%;background:#fff;display:flex;align-items:center;justify-content:center"><svg width="10" height="12" viewBox="0 0 10 12"><path d="M5 1 2 4h6zM5 11 2 8h6z" fill="#141414"/></svg></div>
  <div class="abs stars" style="left:287px;top:54px"><svg width="80" height="14" viewBox="0 0 80 14"><g fill="#f2b824"><path id="st" d="M7 0l2 5h5l-4 3 1.5 5L7 10l-4.5 3L4 8 0 5h5z"/><use href="#st" x="16"/><use href="#st" x="32"/><use href="#st" x="48"/><use href="#st" x="64"/></g></svg></div>
  <h3 class="abs" style="left:287px;top:78px;width:400px">The team at Harrowfield Dentistry made me feel so welcome.</h3>
  <div class="abs" style="left:287px;top:148px;width:400px;height:1px;background:var(--line)"></div>
  <p class="abs q" style="left:287px;top:164px;width:390px">“Lorem ipsum dolor sit amet, consectetuer adipiscing elit, sed diam nonummy nibh euismod tincidunt ut laoreet dolore magna aliquam erat volutpat. Ut wisi enim ad minim.”</p>
  <div class="abs serif" style="left:287px;top:238px;font-size:15px;font-weight:600">-Nadia P.</div>
  <div class="gdot abs" style="left:668px;top:236px"></div>
</div>
<div class="abs rev" style="left:968px;width:280px"><div class="abs" style="left:6px;top:6px;width:290px;height:296px;background:linear-gradient(90deg,#f3ebe7,#d9b2a9)" role="img" aria-label="Before and after smile comparison"></div><div class="abs" style="left:165px;top:6px;width:3px;height:296px;background:#fff"></div><span class="lbl" style="left:14px;top:285px">AFTER</span></div>
<div class="abs dots" style="left:556px;top:2973px"><i><svg width="6" height="8" viewBox="0 0 6 8"><path d="M5 1 2 4l3 3" stroke="#555" fill="none"/></svg></i><i class="on"><svg width="6" height="8" viewBox="0 0 6 8"><path d="m1 1 3 3-3 3" stroke="#fff" fill="none"/></svg></i></div>

<!-- TEAM -->
<h2 class="abs sec-title" style="left:140px;top:3115px">Meet the Harrowfield<br>Dentistry Team</h2>
<div class="btn btn-dark" style="left:857px;top:3147px;width:203px;height:40px;font-size:11px">Schedule Appointment<span class="btn-ic"><svg width="12" height="12" viewBox="0 0 12 12"><path d="M3 9 9 3M4 3h5v5" stroke="#141414" stroke-width="1.6" fill="none"/></svg></span></div>
<div class="abs tm" style="left:140px;width:244px"><div class="ph" role="img" aria-label="Portrait of a female dentist in a white coat"></div><span class="plus">+</span><div class="nm"><b>Dr. Clara Whitfield</b><small>Lead Dentist</small></div></div>
<div class="abs tm" style="left:395px;width:243px"><div class="ph" role="img" aria-label="Portrait of a male dental hygienist"></div><span class="plus">+</span><div class="nm"><b>Owen Marsh, RDH</b><small>Dental Hygienist</small></div></div>
<div class="abs tm" style="left:857px;width:203px"><div class="ph" role="img" aria-label="Portrait of a male dental hygienist"></div><div class="nm" style="left:0"><b style="padding-left:30px">Owen Marsh, RDH</b><small style="padding-left:30px">Dental Hygienist</small></div></div>
<div class="abs" style="left:597px;top:3216px;width:260px;height:386px;background:#fff;border-radius:8px;box-shadow:0 12px 30px rgba(0,0,0,.12);z-index:3">
  <div class="abs" style="left:0;top:-30px;width:260px;height:330px;background:linear-gradient(180deg,rgba(255,255,255,0),#e6e9ec)" role="img" aria-label="Portrait of the office manager with arms crossed"></div>
  <div class="abs" style="left:20px;top:270px;width:220px;height:80px;background:var(--ink);border-radius:6px;color:#fff;padding:24px 0 0 22px"><b style="font-size:16px;display:block">Lena Ortiz</b><small style="font-size:9px">Office Manager</small>
  <span class="abs" style="left:148px;top:28px;width:22px;height:22px;border-radius:50%;background:#333"></span><span class="abs" style="left:176px;top:28px;width:22px;height:22px;border-radius:50%;background:#333"></span></div>
  <span class="abs" style="left:42px;top:258px;width:24px;height:24px;border-radius:50%;background:#fff;border:1px solid #ccc;display:flex;align-items:center;justify-content:center;font-size:16px">−</span>
</div>

<!-- SCHEDULE -->
<h2 class="abs center sec-title" style="top:3710px">Schedule Appointment</h2>
<div class="abs band"></div>
<div class="abs form"></div>
<span class="lab" style="left:271px;top:3893px">First Name*</span>
<span class="lab" style="left:614px;top:3893px">Last Name*</span>
<div class="fld" style="left:271px;top:3916px;width:317px">Owen Marsh, RDH<span class="tick"><svg width="7" height="7" viewBox="0 0 8 8"><path d="m1 4 2 2 4-4" stroke="#fff" fill="none"/></svg></span></div>
<div class="fld" style="left:614px;top:3916px;width:318px">Owen Marsh, RDH</div>
<span class="lab" style="left:271px;top:3981px">Doctor</span>
<span class="lab" style="left:614px;top:3981px">Appointment Date</span>
<div class="fld" style="left:271px;top:4006px;width:317px">Dr. Clara Whitfield<span class="sel"><svg width="6" height="4" viewBox="0 0 6 4"><path d="m1 1 2 2 2-2" stroke="#444" fill="none"/></svg></span></div>
<div class="fld" style="left:614px;top:4006px;width:318px">Monday, 6th April, 25<span class="sel"><svg width="6" height="4" viewBox="0 0 6 4"><path d="m1 1 2 2 2-2" stroke="#444" fill="none"/></svg></span></div>
<span class="lab" style="left:271px;top:4070px">Available Hours</span>
<div class="fld" style="left:271px;top:4092px;width:146px">9:00 AM</div>
<div class="fld" style="left:442px;top:4092px;width:146px">10:00 AM<span class="tick"><svg width="7" height="7" viewBox="0 0 8 8"><path d="m1 4 2 2 4-4" stroke="#fff" fill="none"/></svg></span></div>
<div class="fld" style="left:614px;top:4092px;width:146px">11:00 AM</div>
<div class="fld" style="left:784px;top:4092px;width:148px">1:00 PM</div>
<div class="fld" style="left:271px;top:4154px;width:146px">2:00 PM</div>
<div class="fld" style="left:442px;top:4154px;width:146px">3:00 PM</div>
<div class="fld" style="left:614px;top:4154px;width:146px">4:00 PM</div>
<div class="fld" style="left:784px;top:4154px;width:148px">5:00 PM</div>
<div class="abs confirm">Confirm Date And Time</div>

<!-- FOOTER -->
<footer class="foot">
  <div class="logo" style="left:140px;top:4420px;color:#fff"><div class="l1">Harrowfield</div><div class="l2">DENTISTRY</div></div>
  <div class="abs" style="left:192px;top:4475px;display:flex;gap:12px"><span class="sqsoc"></span><span class="sqsoc"></span></div>
  <h5 style="left:399px;top:4420px">CONTACT US</h5>
  <div class="row" style="left:399px;top:4466px"><svg width="18" height="18" viewBox="0 0 24 24"><path d="M12 2a7 7 0 0 0-7 7c0 5 7 13 7 13s7-8 7-13a7 7 0 0 0-7-7zm0 9.5A2.5 2.5 0 1 1 12 6.5a2.5 2.5 0 0 1 0 5z" fill="none" stroke="#fff" stroke-width="2"/></svg><div>Address<br>88 Willow Crest Road, Brookdale,<br>CA 90210</div></div>
  <div class="row" style="left:399px;top:4525px"><svg width="18" height="18" viewBox="0 0 24 24"><path d="M6.6 10.8a15 15 0 0 0 6.6 6.6l2.2-2.2a1 1 0 0 1 1-.3 11 11 0 0 0 3.6.6 1 1 0 0 1 1 1V20a1 1 0 0 1-1 1A17 17 0 0 1 3 4a1 1 0 0 1 1-1h3.5a1 1 0 0 1 1 1c0 1.3.2 2.5.6 3.6a1 1 0 0 1-.3 1z" fill="#fff"/></svg><div>Call us<br><b>(555) 014-2367</b></div></div>
  <div class="row" style="left:399px;top:4580px"><svg width="18" height="18" viewBox="0 0 24 24"><rect x="3" y="5" width="18" height="14" fill="#fff"/><path d="m3 6 9 7 9-7" stroke="#141414" fill="none"/></svg><div>Email us<br><b style="font-size:11px;text-decoration:underline">hello@harrowfielddental.com</b></div></div>
  <div class="row" style="left:399px;top:4632px"><svg width="18" height="18" viewBox="0 0 24 24"><circle cx="12" cy="12" r="9" fill="none" stroke="#fff" stroke-width="2"/><path d="M12 7v5l3 2" stroke="#fff" stroke-width="2" fill="none"/></svg><div>Business Hours<br>Monday – Friday: <b style="font-size:10px">8:00 AM – 5:00 PM</b><br>Saturday: <b style="font-size:10px">9:00 AM – 2:00 PM</b><br>Sunday: <b style="font-size:10px">Closed</b></div></div>
  <h5 style="left:713px;top:4420px">LINKS</h5>
  <ul style="left:713px;top:4455px"><li>Home</li><li>About us</li><li>Services</li><li>Procedures</li><li>Testimonials</li><li>Why Choose Us</li><li>Contact us</li></ul>
  <h5 style="left:880px;top:4420px">OUR LOCATION</h5>
  <div class="abs map" role="img" aria-label="Street map showing the clinic location"></div>
  <div class="abs" style="left:0;top:4770px;width:1200px;height:1px;background:#333"></div>
  <div class="abs center" style="top:4784px;font-size:10px;color:#bbb">©2025 HARROWFIELD DENTISTRY. ALL RIGHTS RESERVED.</div>
</footer>

</body>
</html>
```